Personalized Technology Company Needs a Business Card

I need a double-sided business card. Both sides will have the logo, and the contact information. One side will be black, with the white / gray logo, and the other will be white, with the black / gray logo. The black side will have the text "Custom Gaming PC's" and will have a water-cooled gaming PC image. The white side will have the text "Custom Business Computers & Consulting", and will have a business / enterprise PC image. Feel free to add a conservative image in the background, while the color remains unchanged. I'm uploading the base logo (transparent), so you can modify the colors, both the finished colored logos and an idea of ​​the business card (with the current information, just missing the website, which is www.velomindsystems.com, please add it.) Thank you so much for your effort, I'll be specting your cool designs. Good Luck!

Target Market(s)

Gamers & Entrepreneurs / Business Owners / Chief Technology Officers

Industry/Entity Type

Technology Equipment

Contact Information for Business Card

I need a double-sided business card. Both sides will have the logo, and the contact information. One side will be black, with the white/gray logo, and the other one will be white, with the black/gray logo. The black side will have the text "Custom Gaming PC's" and will have a water-cooled gaming PC image. The white side will have the text "Custom Business Computers & Consulting", and will have a business/enterprise PC image. Feel free to add a conservative image in the background, whilst the color remains unchanged.

I'm uploading the base logo (transparent), so you can modify the colors, both the finished colored logos and an idea of the business card (with the actual information, just missing the website, which is www.velomindsystems.com, please add it.)

Thank you so much for your effort, I'll be specting your cool designs. Good Luck!

Font styles to use
Serif

Colors
000000
757575
ffffff

Requirements
Must have
• Please See Description
Nice to have
• Please See Description
Should not have
• Please See Description

```html
<!DOCTYPE html>
<html lang="en">
<head>
<meta charset="utf-8">
<title>Velomind Systems – Business Card</title>
<link href="https://fonts.googleapis.com/css2?family=Lato:ital,wght@0,400;0,700;1,400;1,700&display=swap" rel="stylesheet">
<style>
  :root {
    --backdrop: #8a8a8a;
    --card-white: #ffffff;
    --ink: #111111;
    --accent-blue: #1a3fd6;
    --rule-grey: #c8c8c8;
    --dark-top: #3c3c3c;
    --dark-mid: #2e2e2e;
    --dark-bottom: #1f1f1f;
    --mark-light: #e4ded4;
  }
  * { box-sizing: border-box; margin: 0; padding: 0; }
  html, body {
    width: 1200px; height: 900px; overflow: hidden;
    background: var(--backdrop);
    font-family: "Lato", Arial, sans-serif;
  }
  .canvas { position: relative; width: 1200px; height: 900px; }
  .card {
    position: absolute; top: 170px;
    width: 347px; height: 561px;
  }
  .card-front { left: 259px; background: var(--card-white); color: var(--ink); text-align: center; }
  .card-back { left: 631px; background: var(--dark-bottom); overflow: hidden; }

  .brand {
    position: absolute; top: 88px; left: 0; right: 0;
    display: flex; align-items: center; justify-content: center; gap: 12px;
  }
  .brand-square { width: 34px; height: 34px; background: var(--ink); }
  .brand-name { font-size: 24px; font-weight: 700; letter-spacing: 2px; color: var(--ink); }
  .tagline {
    position: absolute; top: 214px; left: 0; right: 0;
    font-size: 14px; font-style: italic; font-weight: 400; letter-spacing: 0.2px;
  }
  .person { position: absolute; top: 321px; left: 0; right: 0; }
  .person-name { font-size: 20px; color: var(--accent-blue); letter-spacing: 0.5px; }
  .person-role { font-size: 14px; margin-top: 2px; }
  .rule { position: absolute; left: 62px; width: 222px; height: 1px; background: var(--rule-grey); }
  .rule-top { top: 381px; }
  .rule-bottom { top: 492px; }
  .contact {
    position: absolute; top: 398px; left: 0; right: 0;
    font-size: 15px; line-height: 20px; list-style: none;
  }
  .contact-label { color: var(--accent-blue); font-weight: 700; }
  .contact-web { color: var(--accent-blue); }
  .service { position: absolute; top: 507px; left: 0; right: 0; font-size: 16px; letter-spacing: 1px; }

  .back-pattern {
    position: absolute; inset: 0;
    background: linear-gradient(180deg, var(--dark-top) 0%, var(--dark-mid) 55%, var(--dark-bottom) 100%);
  }
  .back-mark {
    position: absolute; top: 186px; left: 206px; width: 130px;
    display: flex; flex-direction: column; align-items: center; gap: 8px;
  }
  .back-mark-square { width: 26px; height: 26px; background: var(--mark-light); }
  .back-mark-name { font-size: 10px; font-weight: 700; letter-spacing: 1px; color: var(--mark-light); white-space: nowrap; }
</style>
</head>
<body>
<main class="canvas">
  <section class="card card-front">
    <div class="brand">
      <span class="brand-square"></span>
      <span class="brand-name">VELOMIND SYSTEMS</span>
    </div>
    <p class="tagline">CUSTOM BUSINESS COMPUTERS &amp; CONSULTING</p>
    <div class="person">
      <p class="person-name">MARCO RUIZ DELGADO</p>
      <p class="person-role">CEO &amp; Co-Founder</p>
    </div>
    <div class="rule rule-top"></div>
    <ul class="contact">
      <li><span class="contact-label">P:</span> 52 5810-3274</li>
      <li><span class="contact-label">M:</span> +52 55-4916-0583</li>
      <li><span class="contact-label">E:</span> contact@velomindsystems.com</li>
      <li class="contact-web">www.velomindsystems.com</li>
    </ul>
    <div class="rule rule-bottom"></div>
    <p class="service">CUSTOM GAMING PC'S</p>
  </section>

  <section class="card card-back">
    <div class="back-pattern" role="img" aria-label="Faint repeating brand-mark pattern on charcoal, fading toward the bottom"></div>
    <div class="back-mark">
      <span class="back-mark-square"></span>
      <span class="back-mark-name">VELOMIND SYSTEMS</span>
    </div>
  </section>
</main>
</body>
</html>
```